Halvex Power

We need a business card for "Halvex power". I have uploaded the logo, the color of the card should be according to the logo "Blackish".
Basically halvex power is a solar company.
Also we would like a sample file in which we can edit the information such names and contact details ourselves
The card would be two sided with following details
1- logo on front and underneath the logo there should be a line saying
"Cleaner . Cheaper . Power"
2-website i.e "www.halvexpowerco.com"
3- Icons for Facebook and Instagram that tells the clients we are available on both social sites.
4- name of the person with his/her designation underneath and email address
5-contact number
6- 1-800--- number with the extension number

its up to the designer how he/she places the details,but it must look professional

Industry/Entity Type

Business

Contact Information for Business Card

5-contact number

Requirements
Must have
• 1- logo on front and underneath the logo there should be a line saying
• "Cleaner . Cheaper . Power"
• 2-website i.e "www.halvexpowerco.com"
• 3- Icons for Facebook and Instagram that tells the clients we are available on both social sites.
• 4- name of the person with his/her designation underneath and email address
• 5-contact number of the person
• 6- 1-800--- number with the extension number
• 7-card should be in black shade like the logo

```html
<!DOCTYPE html>
<html lang="en">
<head>
<meta charset="utf-8">
<title>Halvex Power – Business Card</title>
<link href="https://fonts.googleapis.com/css2?family=Open+Sans:wght@400;600;700&display=swap" rel="stylesheet">
<style>
  :root {
    --backdrop: #2b2b2b;
    --card-light: #f4f4f2;
    --card-dark: #141414;
    --brand-green: #7cc242;
    --ink: #3a3a3a;
    --ink-soft: #555555;
    --ink-muted: #8a8a8a;
    --rule: #4a4a4a;
    --social: #3b5b98;
  }
  * { box-sizing: border-box; margin: 0; padding: 0; }
  html, body { width: 1200px; height: 900px; overflow: hidden; }
  body {
    background: var(--backdrop);
    font-family: "Open Sans", Arial, sans-serif;
    display: flex;
    align-items: center;
    justify-content: center;
    gap: 40px;
  }
  .card {
    width: 540px;
    height: 310px;
    border-radius: 22px;
    position: relative;
    box-shadow: 0 10px 30px rgba(0,0,0,.35);
  }
  .card--front { background: var(--card-light); color: var(--ink); }
  .card--back {
    background: var(--card-dark);
    display: flex;
    align-items: center;
    justify-content: center;
  }

  .brand-block { display: flex; flex-direction: column; align-items: flex-end; gap: 4px; }
  .card--front .brand-block { position: absolute; top: 34px; right: 40px; }
  .card--back .brand-block { align-items: center; gap: 8px; }

  .brand { display: flex; align-items: center; gap: 10px; }
  .brand__dot { width: 22px; height: 22px; border-radius: 50%; background: var(--brand-green); }
  .brand__name {
    font-weight: 700;
    color: var(--brand-green);
    font-size: 30px;
    line-height: 38px;
    letter-spacing: .3px;
  }
  .card--back .brand__name { font-size: 36px; line-height: 44px; }
  .card--back .brand__dot { width: 26px; height: 26px; }

  .tagline {
    font-size: 11px;
    font-weight: 600;
    letter-spacing: 2.5px;
    text-transform: uppercase;
    color: var(--ink-soft);
  }
  .card--back .tagline { color: var(--ink-muted); font-size: 12px; letter-spacing: 3px; }

  .social {
    position: absolute; top: 112px; right: 40px;
    display: flex; gap: 6px;
  }
  .social__box { width: 18px; height: 18px; background: var(--social); border-radius: 2px; }

  .divider {
    position: absolute; top: 138px; left: 150px; right: 40px;
    height: 1px; background: var(--rule);
  }

  .web-info {
    position: absolute; top: 152px; right: 40px;
    text-align: right; font-size: 13px; line-height: 22px; color: var(--ink);
  }
  .web-info li { list-style: none; display: flex; align-items: center; justify-content: flex-end; gap: 6px; }
  .web-info svg { width: 11px; height: 11px; fill: var(--brand-green); }

  .person { position: absolute; left: 40px; top: 188px; }
  .person__name {
    font-size: 18px; font-weight: 600; letter-spacing: .5px; text-transform: uppercase;
    display: flex; align-items: center; gap: 10px;
  }
  .person__first { color: var(--brand-green); }
  .person__last { color: var(--ink); }
  .person__rule { width: 130px; height: 1px; background: var(--rule); }
  .person__title { font-size: 13px; color: var(--ink-soft); margin-top: 1px; }

  .phones { position: absolute; left: 40px; top: 250px; font-size: 14px; line-height: 20px; color: var(--ink); }
  .phones li { list-style: none; display: flex; align-items: center; gap: 8px; }
  .phones svg { width: 12px; height: 12px; fill: var(--brand-green); }
</style>
</head>
<body>
  <section class="card card--front" aria-label="Business card front">
    <div class="brand-block">
      <div class="brand">
        <span class="brand__dot"></span>
        <span class="brand__name">Halvex Power</span>
      </div>
      <p class="tagline">Cleaner . Cheaper . Power</p>
    </div>

    <div class="social" aria-label="Social profiles">
      <span class="social__box"></span>
      <span class="social__box"></span>
    </div>

    <div class="divider"></div>

    <ul class="web-info">
      <li>info@halvexpowerco.com
        <svg viewBox="0 0 12 12"><rect x="0" y="2" width="12" height="8" rx="1"/></svg></li>
      <li>www.halvexpowerco.com
        <svg viewBox="0 0 12 12"><circle cx="6" cy="6" r="6"/></svg></li>
    </ul>

    <div class="person">
      <p class="person__name">
        <span><span class="person__first">Daniel</span> <span class="person__last">Marsh</span></span>
        <span class="person__rule"></span>
      </p>
      <p class="person__title">Managing Director</p>
    </div>

    <ul class="phones">
      <li><svg viewBox="0 0 12 12"><rect x="3" y="0" width="6" height="12" rx="1"/></svg>044-555 010 203</li>
      <li><svg viewBox="0 0 12 12"><path d="M1 5 Q6 0 11 5 L9 6 Q6 4 3 6 Z M3 7 H9 V11 H3 Z"/></svg>1-800-555-0142 ext. 204</li>
    </ul>
  </section>

  <section class="card card--back" aria-label="Business card back">
    <div class="brand-block">
      <div class="brand">
        <span class="brand__dot"></span>
        <span class="brand__name">Halvex Power</span>
      </div>
      <p class="tagline">Cleaner . Cheaper . Power</p>
    </div>
  </section>
</body>
</html>
```